Investment company needing business card

We are wanting a business card which looks sharp and easy on the eye. We are thinking of having a business card with the logo embossed on it, to really make it stand out. We will only have a small amount of information of the business card, person's name, position, email address and phone number

Contact Information for Business Card

Danielle Frost
Executive Assistant
+64 21 473 5162
danielf@harwickpartners.co.nz

Requirements
Must have
• Embossed logo
Should not have
• Not to be busy

```html
<!DOCTYPE html>
<html lang="en">
<head>
<meta charset="utf-8">
<title>Harwick Partners — Business Card</title>
<link rel="stylesheet" href="https://fonts.googleapis.com/css2?family=Open+Sans:wght@400;700&display=swap">
<style>
  :root {
    --backdrop: #2b2b2b;
    --card-white: #ffffff;
    --card-dark: #2f2f2f;
    --brand-green: #1fae5f;
    --brand-grey: #6b6b6b;
    --text-grey: #555555;
    --rule-grey: #9a9a9a;
    --on-dark: #ffffff;
  }
  * { box-sizing: border-box; margin: 0; padding: 0; }
  html, body {
    width: 1200px; height: 900px; overflow: hidden;
    background: var(--backdrop);
    font-family: "Open Sans", Arial, sans-serif;
  }
  .stage {
    width: 1200px; height: 900px;
    display: flex; flex-direction: column; align-items: center; justify-content: center;
    gap: 40px;
  }
  .card {
    position: relative;
    width: 700px; height: 400px;
    border-radius: 22px;
    overflow: hidden;
  }
  /* Front */
  .card-front { background: var(--card-white); }
  .front-wordmark {
    position: absolute; left: 50px; top: 168px;
    display: flex; align-items: center; gap: 14px;
  }
  .wordmark-square {
    width: 40px; height: 40px; background: var(--brand-green);
  }
  .wordmark-name {
    font-weight: 700; font-size: 27px; letter-spacing: 2px;
    color: var(--brand-green); text-transform: uppercase; line-height: 1.1;
  }
  .divider {
    position: absolute; left: 350px; top: 105px;
    width: 1px; height: 150px; background: var(--rule-grey);
  }
  .contact {
    position: absolute; left: 378px; top: 108px;
    color: var(--text-grey);
  }
  .contact-name {
    font-weight: 700; font-size: 22px; color: var(--brand-green);
    text-transform: uppercase; letter-spacing: 0.3px;
  }
  .contact-title { font-size: 16px; margin-bottom: 18px; }
  .contact-list { list-style: none; }
  .contact-row {
    display: flex; align-items: center; gap: 10px;
    font-size: 16px; line-height: 26px;
  }
  .contact-row svg { width: 14px; height: 14px; flex: none; }
  .band {
    position: absolute; left: 0; bottom: 0; width: 100%; height: 12px;
    display: flex;
  }
  .band-grey { width: 62%; background: var(--brand-grey); }
  .band-green { flex: 1; background: var(--brand-green); }
  /* Back */
  .card-back {
    background: var(--card-dark);
    display: flex; align-items: center; justify-content: center;
  }
  .back-wordmark { display: flex; align-items: center; gap: 22px; }
  .back-wordmark .wordmark-square {
    width: 70px; height: 70px; background: var(--on-dark);
  }
  .back-wordmark .wordmark-name {
    color: var(--on-dark); font-size: 44px; letter-spacing: 3px;
  }
</style>
</head>
<body>
<main class="stage">
  <section class="card card-front" aria-label="Business card front">
    <div class="front-wordmark">
      <span class="wordmark-square"></span>
      <span class="wordmark-name">Harwick<br>Partners</span>
    </div>
    <div class="divider"></div>
    <div class="contact">
      <p class="contact-name">Danielle Frost</p>
      <p class="contact-title">Executive Assistant</p>
      <ul class="contact-list">
        <li class="contact-row">
          <svg viewBox="0 0 24 24" aria-hidden="true"><path fill="#1fae5f" d="M6.6 10.8a15.1 15.1 0 0 0 6.6 6.6l2.2-2.2a1 1 0 0 1 1-.25 11.4 11.4 0 0 0 3.6.57 1 1 0 0 1 1 1V20a1 1 0 0 1-1 1A17 17 0 0 1 3 4a1 1 0 0 1 1-1h3.5a1 1 0 0 1 1 1c0 1.25.2 2.45.57 3.57a1 1 0 0 1-.25 1z"/></svg>
          +64 21 473 5162
        </li>
        <li class="contact-row">
          <svg viewBox="0 0 24 24" aria-hidden="true"><rect x="2" y="5" width="20" height="14" rx="1" fill="#1fae5f"/><path d="M2 6l10 7 10-7" fill="none" stroke="#fff" stroke-width="1.8"/></svg>
          danielf@harwickpartners.co.nz
        </li>
        <li class="contact-row">
          <svg viewBox="0 0 24 24" aria-hidden="true"><circle cx="12" cy="12" r="10" fill="#1fae5f"/><path d="M2 12h20M12 2c3 3 3 17 0 20M12 2c-3 3-3 17 0 20" fill="none" stroke="#fff" stroke-width="1.4"/></svg>
          www.harwickpartners.co.nz
        </li>
      </ul>
    </div>
    <div class="band"><span class="band-grey"></span><span class="band-green"></span></div>
  </section>

  <section class="card card-back" aria-label="Business card back">
    <div class="back-wordmark">
      <span class="wordmark-square"></span>
      <span class="wordmark-name">Harwick<br>Partners</span>
    </div>
  </section>
</main>
</body>
</html>
```